Website design for legal tech start up in Switzerland (B2B)

We are for a legal tech start up in Switzerland called KOVA. We have been running since August 2016. This will be our first live website.

We need a website designed and business card design for our start-up in Switzerland. We also need the Web design to be converted into HTML and CSS files.

Function of website:
• To inform potential customers of our services
• Form a key part of our digital marketing and sales footprint.
• Branding

Please find attached logo.
Updates

Project Deadline Extended Reason: Giving us time to review submissions and provide opportunity for more submissions. Added Thursday, February 16, 2017

Project Deadline Extended
Reason: Looking for more idea's not necessarily set on blue and grey colours only.

Target Market(s)

B2B tech powered legal services.

Industry/Entity Type

Legal

Contact Information for Business Card

Lean and slick design.

Coding

Coded - Design and coding required

Number of Pages Required

5+ page

Requirements
Must have
• VERY LEAN AND CLEAN DESIGN!
• We have received many great standard designs, but we are looking for something more out-of-the box: You can get inspiration from these designs: http://www.pixelvane.com/websites/clean/
• Thanks!!
• Easy content management system
• Well structured coding for additional development
• Responsive webpage for all types of devices
• SEO optimized
• Tabs (Home, services, team, careers, blog, contact us)
• Colour scheme complementary to logo
Nice to have
• Look and Design - Approachable, High-tech, Modern
• Easy to add chat bot capability in future
Should not have
• Too busy/ too much clutter
• Not take to long to load

```html
<!DOCTYPE html>
<html lang="en">
<head>
<meta charset="utf-8">
<title>KOVA – Legal Services</title>
<link href="https://fonts.googleapis.com/css2?family=Open+Sans:wght@400;600;700&family=Raleway:wght@600;700&display=swap" rel="stylesheet">
<style>
:root{
  --ink:#2f3b44;
  --text:#6d747a;
  --muted:#9aa0a5;
  --accent:#2c3e50;
  --blue:#2f6fb3;
  --band:#f2f3f4;
  --line:#d9dcdf;
  --footer:#3b3f42;
  --footer-bottom:#2e3134;
  --footer-text:#b9bdc0;
  --white:#ffffff;
}
*{margin:0;padding:0;box-sizing:border-box}
html,body{width:1200px;height:2168px;overflow:hidden;background:var(--white)}
body{font-family:"Open Sans",Arial,sans-serif;color:var(--text);font-size:13px}
.wrap{width:960px;margin:0 auto;position:relative}

.site-header{height:96px}
.site-header .wrap{display:flex;align-items:center;justify-content:space-between;height:96px}
.logo{display:flex;align-items:center;gap:10px;font-family:"Raleway",sans-serif;font-weight:700;font-size:40px;letter-spacing:2px;color:var(--ink)}
.logo-mark{width:14px;height:14px;background:var(--ink)}
.nav{display:flex;gap:30px;list-style:none}
.nav a{font-size:11px;font-weight:600;letter-spacing:.5px;color:var(--muted);text-decoration:none}
.nav a.active{color:var(--ink)}

.hero{height:486px;background:linear-gradient(180deg,#d6e2ee 0%,#c9d6e2 35%,#b98e70 55%,#8d7a66 75%,#6a7e87 100%)}

.welcome{height:348px;text-align:center;padding-top:92px}
.section-title{font-family:"Raleway",sans-serif;font-weight:700;font-size:24px;color:var(--ink);letter-spacing:.5px}
.rule{width:44px;height:2px;background:var(--ink);margin:12px auto 18px}
.welcome p{width:960px;margin:0 auto;font-size:12.5px;line-height:20px;text-align:justify}
.btn{display:inline-block;border:1px solid var(--line);padding:7px 16px;font-size:10.5px;color:var(--text);text-decoration:none;background:var(--white)}
.welcome .btn{margin-top:22px}

.services{height:412px;background:var(--band);text-align:center;padding-top:88px}
.service-grid{display:flex;justify-content:space-between;margin-top:8px}
.service{width:210px}
.service svg{display:block;margin:0 auto 12px}
.service h3{font-family:"Raleway",sans-serif;font-weight:700;font-size:19px;color:var(--ink);margin-bottom:10px}
.service p{font-size:11.5px;line-height:17px;margin-bottom:18px}

.blog{height:448px;padding-top:78px}
.blog-head{display:flex;justify-content:space-between;align-items:center;margin-bottom:20px}
.blog-head h2{font-family:"Raleway",sans-serif;font-weight:700;font-size:22px;color:var(--ink)}
.arrows{display:flex;gap:4px}
.arrows span{width:22px;height:22px;border:1px solid var(--line);display:flex;align-items:center;justify-content:center}
.posts{display:flex;justify-content:space-between}
.post{width:308px}
.post-media{height:170px;position:relative}
.m1{background:linear-gradient(160deg,#b7bcc2,#6b7178)}
.m2{background:linear-gradient(160deg,#e9e6e1,#9b8f84)}
.m3{background:linear-gradient(160deg,#c8b49a,#6f7f88)}
.play{position:absolute;left:50%;top:50%;transform:translate(-50%,-50%)}
.post h4{font-size:14px;font-weight:600;color:var(--ink);line-height:19px;margin:14px 0 8px}
.post p{font-size:11px;line-height:16px;margin-bottom:12px}
.meta{display:flex;gap:18px;font-size:10px;color:var(--muted)}
.meta span{display:flex;align-items:center;gap:5px}
.meta i{display:inline-block;width:8px;height:8px;background:var(--muted)}

.site-footer{height:340px;background:var(--footer);color:var(--footer-text);padding-top:28px}
.footer-cols{display:flex;justify-content:space-between}
.site-footer h5{font-size:13px;font-weight:600;color:var(--white);margin-bottom:18px}
.contact-list{list-style:none;font-size:10.5px;line-height:15px}
.contact-list li{display:flex;gap:8px;margin-bottom:12px}
.contact-list svg{flex:none;margin-top:2px}
.map{width:150px;height:92px;background:linear-gradient(135deg,#e4e4e0,#cfd3cf);margin-top:38px}
.links{display:flex;gap:40px}
.links ul{list-style:none;font-size:10.5px;line-height:22px}
.links li::before{content:"› ";}
.social{display:grid;grid-template-columns:repeat(2,22px);gap:8px}
.social span{width:22px;height:22px;display:block}
.copyright{position:absolute;left:0;right:0;top:2130px;height:38px;background:var(--footer-bottom);text-align:center;font-size:10px;line-height:38px;color:var(--footer-text)}
</style>
</head>
<body>
<header class="site-header">
  <div class="wrap">
    <div class="logo"><span class="logo-mark"></span>KOVA</div>
    <ul class="nav">
      <li><a class="active" href="#">HOME</a></li>
      <li><a href="#">SERVICES</a></li>
      <li><a href="#">TEAM</a></li>
      <li><a href="#">CAREERS</a></li>
      <li><a href="#">BLOG</a></li>
      <li><a href="#">CONTACT US</a></li>
    </ul>
  </div>
</header>

<section class="hero" role="img" aria-label="Photograph of a Swiss old town with towers and historic buildings by a river"></section>

<section class="welcome">
  <h1 class="section-title">WELCOME TO KOVA</h1>
  <div class="rule"></div>
  <p>Kova helps growing businesses handle their legal work with clarity and speed. Our team combines trusted lawyers with smart digital tools so that contracts, advice and filings move without friction. We work with startups and established firms across Switzerland, offering fixed prices, quick answers and plain language. From company setup to daily contracts, employment matters and disputes, we keep your legal tasks simple, secure and visible. Every client receives a dedicated contact, an online workspace and clear updates at each step, so you always know where things stand and what comes next for your business.</p>
  <a class="btn" href="#">Read more</a>
</section>

<section class="services">
  <div class="wrap">
    <h2 class="section-title">OUR SERVICES</h2>
    <div class="rule"></div>
    <div class="service-grid">
      <div class="service">
        <svg width="34" height="30" viewBox="0 0 34 30"><circle cx="9" cy="7" r="5" fill="#2f6fb3"/><circle cx="25" cy="7" r="5" fill="#2f6fb3"/><circle cx="17" cy="12" r="4" fill="#2f6fb3"/><path d="M1 26a8 8 0 0 1 16 0z M17 26a8 8 0 0 1 16 0z M10 29a7 7 0 0 1 14 0z" fill="#2f6fb3"/></svg>
        <h3>FAMILY LAW</h3>
        <p>Guidance on marriage, custody and inheritance with care and discretion for every family.</p>
        <a class="btn" href="#">READ MORE</a>
      </div>
      <div class="service">
        <svg width="34" height="30" viewBox="0 0 34 30"><rect x="11" y="2" width="12" height="6" rx="1" fill="none" stroke="#2f6fb3" stroke-width="2.5"/><rect x="1" y="8" width="32" height="20" rx="2" fill="#2f6fb3"/><rect x="15" y="15" width="4" height="4" fill="#fff"/></svg>
        <h3>BUSINESS LAW</h3>
        <p>Company formation, contracts and compliance support that keeps your business moving.</p>
        <a class="btn" href="#">READ MORE</a>
      </div>
      <div class="service">
        <svg width="34" height="30" viewBox="0 0 34 30"><path d="M6 12l4-9h14l4 9h3v10h-3v5h-5v-5H11v5H6v-5H3V12z" fill="#2f6fb3"/><rect x="11" y="6" width="12" height="6" fill="#fff"/><circle cx="9" cy="17" r="2" fill="#fff"/><circle cx="25" cy="17" r="2" fill="#fff"/></svg>
        <h3>VEHICLE LAW</h3>
        <p>Help with accidents, traffic offences, insurance claims and vehicle purchase disputes.</p>
        <a class="btn" href="#">READ MORE</a>
      </div>
      <div class="service">
        <svg width="34" height="30" viewBox="0 0 34 30"><rect x="1" y="5" width="32" height="20" rx="2" fill="#2f6fb3"/><circle cx="17" cy="15" r="6" fill="#fff"/><rect x="16" y="11" width="2" height="8" fill="#2f6fb3"/></svg>
        <h3>DEBT LAW</h3>
        <p>Advice on collections, restructuring and settlements for creditors and debtors alike.</p>
        <a class="btn" href="#">READ MORE</a>
      </div>
    </div>
  </div>
</section>

<section class="blog">
  <div class="wrap">
    <div class="blog-head">
      <h2>BLOG</h2>
      <div class="arrows">
        <span><svg width="8" height="10" viewBox="0 0 8 10"><path d="M6 1L2 5l4 4" stroke="#9aa0a5" stroke-width="1.5" fill="none"/></svg></span>
        <span><svg width="8" height="10" viewBox="0 0 8 10"><path d="M2 1l4 4-4 4" stroke="#9aa0a5" stroke-width="1.5" fill="none"/></svg></span>
      </div>
    </div>
    <div class="posts">
      <article class="post">
        <div class="post-media m1" role="img" aria-label="Photograph of a classical courthouse facade with columns"></div>
        <h4>Donec scelerisque felis at ante rhoncus, non mattis nulla facilisis</h4>
        <p>Integer pretium risus vitae nisi tincidunt, eu tempus lorem aliquet. Fusce vel sapien at magna finibus luctus non vitae purus.</p>
        <div class="meta"><span><i></i>256</span><span><i></i>24</span><span><i></i>5 APRIL 2017</span></div>
      </article>
      <article class="post">
        <div class="post-media m2" role="img" aria-label="Photograph of a desk with documents, pen and a judge's gavel"></div>
        <h4>Donec scelerisque felis at ante rhoncus, non mattis nulla facilisis</h4>
        <p>Integer pretium risus vitae nisi tincidunt, eu tempus lorem aliquet. Fusce vel sapien at magna finibus luctus non vitae purus.</p>
        <div class="meta"><span><i></i>256</span><span><i></i>24</span><span><i></i>5 APRIL 2017</span></div>
      </article>
      <article class="post">
        <div class="post-media m3" role="img" aria-label="Video still of a Swiss riverside town">
          <svg class="play" width="40" height="40" viewBox="0 0 40 40"><circle cx="20" cy="20" r="20" fill="#fff"/><path d="M16 12l12 8-12 8z" fill="#2f3b44"/></svg>
        </div>
        <h4>Donec scelerisque felis at ante rhoncus, non mattis nulla facilisis</h4>
        <p>Integer pretium risus vitae nisi tincidunt, eu tempus lorem aliquet. Fusce vel sapien at magna finibus luctus non vitae purus.</p>
        <div class="meta"><span><i></i>256</span><span><i></i>24</span><span><i></i>5 APRIL 2017</span></div>
      </article>
    </div>
  </div>
</section>

<footer class="site-footer">
  <div class="wrap footer-cols">
    <div style="display:flex;gap:30px">
      <div>
        <h5>Contact info</h5>
        <ul class="contact-list">
          <li><svg width="10" height="12" viewBox="0 0 10 12"><path d="M5 0a4 4 0 0 1 4 4c0 3-4 8-4 8S1 7 1 4a4 4 0 0 1 4-4z" fill="#b9bdc0"/></svg>12 Lindenweg<br>8001 Zurich</li>
          <li><svg width="10" height="10" viewBox="0 0 10 10"><path d="M2 0l2 2-1 2a6 6 0 0 0 3 3l2-1 2 2-2 2C4 10 0 6 0 2z" fill="#b9bdc0"/></svg>+41 44 555 01 20</li>
          <li><svg width="10" height="10" viewBox="0 0 10 10"><path d="M2 0l2 2-1 2a6 6 0 0 0 3 3l2-1 2 2-2 2C4 10 0 6 0 2z" fill="#b9bdc0"/></svg>+41 44 555 01 21</li>
          <li><svg width="11" height="8" viewBox="0 0 11 8"><rect width="11" height="8" fill="#b9bdc0"/><path d="M0 0l5.5 4L11 0" stroke="#3b3f42" fill="none"/></svg>hello@kova-legal.ch</li>
        </ul>
      </div>
      <div class="map" role="img" aria-label="Street map showing the office location"></div>
    </div>
    <div>
      <h5>Links</h5>
      <div class="links">
        <ul><li>Home</li><li>Services</li><li>Team</li><li>Careers</li><li>Blog</li></ul>
        <ul><li>Contact us</li><li>Terms and conditions</li><li>Privacy policy</li><li>Imprint</li></ul>
      </div>
    </div>
    <div>
      <h5>Social Media</h5>
      <div class="social">
        <span style="background:#3b5998"></span><span style="background:#1da1f2"></span>
        <span style="background:#0077b5"></span><span style="background:#dd4b39"></span>
      </div>
    </div>
  </div>
</footer>
<div class="copyright">Copyright © 2017 KOVA Legal. All rights reserved.</div>
</body>
</html>
```